Website for IT consulting Company

I need a website upgrade, the existing site content is ok, I would also like to add a testimonial page, the site should be something that is easy for us to update content. You use the content from www.kelvanbrook.com as an example. I will also post update logo and artwork. I also need a contact form with some type of validation or captcha.

I added Coded to the Project

Please omit Address maps

Target Market(s)

small business, service oriented companies. We provide IT Consulting, support and mangement

Industry/Entity Type

Information Technology

Coding

Number of Pages Required

1 page

Font styles to use
Serif
Sans Serif

Requirements
Must have
• Contain logo attached, and content from existing web site www.kelvanbrook.com.
• Also need to update content easily, and be movable to different platforms.
• There is a catch phrase
• "Let us worry about your technology…” “ so you don’t have to!”
• Should be included.
Nice to have
• Testimonial page, Project page where we can post new and past projects and pictures
Should not have
• none

```html
<!DOCTYPE html>
<html lang="en">
<head>
<meta charset="utf-8">
<title>Kelvanbrook – IT Consulting</title>
<link href="https://fonts.googleapis.com/css2?family=Montserrat:wght@400;500;600&family=Nunito+Sans:wght@400;600&family=Open+Sans:wght@400;600&display=swap" rel="stylesheet">
<style>
:root{
  --blue:#1a86d6;
  --blue-dark:#0f6fbf;
  --blue-title:#1b7fcc;
  --menu:#2a90dc;
  --ink:#333;
  --muted:#8a8a8a;
  --light-gray:#ededed;
  --line:#cfcfcf;
  --white:#fff;
}
*{box-sizing:border-box;margin:0;padding:0}
html,body{width:1200px;height:3125px;overflow:hidden}
body{position:relative;font-family:"Open Sans",sans-serif;color:var(--ink);background:var(--white)}
section,footer,header{position:absolute;left:0;width:1200px;overflow:hidden}
.abs{position:absolute}

/* hero */
.hero{top:0;height:621px}
.hero-photo{position:absolute;inset:0;background:radial-gradient(ellipse at 75% 55%,#c9a48e 0%,#8a6f6a 14%,#2c4a86 38%,#10244f 65%,#050d22 100%)}
.brand{position:absolute;left:129px;top:30px;display:flex;align-items:center;gap:10px}
.brand-mark{width:30px;height:30px;background:#3fa0e8}
.brand-name{font-family:"Montserrat",sans-serif;font-weight:600;font-size:36px;color:#cfd8e6;letter-spacing:1px}
.menu-toggle{position:absolute;left:1000px;top:38px;width:40px}
.menu-toggle span{display:block;height:3px;background:var(--white);margin-bottom:5px}
.menu{position:absolute;left:848px;top:92px;width:219px;background:var(--menu);list-style:none;z-index:3}
.menu::before{content:"";position:absolute;top:-10px;left:160px;border:10px solid transparent;border-top:0;border-bottom-color:var(--menu)}
.menu li{height:37.5px;line-height:37.5px;padding-left:26px;font-family:"Montserrat",sans-serif;font-size:14px;color:var(--white);border-bottom:1px solid rgba(255,255,255,.25);position:relative}
.menu li:last-child{border-bottom:0}
.menu .has-sub::after{content:"";position:absolute;right:18px;top:14px;width:8px;height:8px;border-top:2px solid var(--white);border-right:2px solid var(--white);transform:rotate(45deg)}
.hero-title{position:absolute;left:0;width:1200px;top:254px;text-align:center;font-family:"Montserrat",sans-serif;font-weight:500;font-size:35px;line-height:40px;color:var(--white);letter-spacing:.5px;z-index:1}
.btn-ghost{position:absolute;left:506px;top:354px;width:192px;height:44px;border:2px solid var(--white);color:var(--white);font-family:"Montserrat",sans-serif;font-size:16px;font-weight:500;text-align:center;line-height:40px}
.dots{position:absolute;top:580px;left:0;width:1200px;display:flex;justify-content:center;gap:8px}
.dots i{width:14px;height:14px;border-radius:50%;background:var(--white)}
.dots i:first-child{background:transparent;border:2px solid var(--white)}

/* about */
.about{top:621px;height:421px}
.about-art{position:absolute;left:0;top:0;width:500px;height:421px;background:radial-gradient(circle at 40% 60%,#e5e8ec 0%,#b9c0c9 35%,#2f86df 55%,#fff 75%)}
.about h2{position:absolute;left:537px;top:80px;font-family:"Nunito Sans",sans-serif;font-weight:400;font-size:28px;color:#222;white-space:nowrap}
.about p{position:absolute;left:537px;top:128px;width:535px;font-size:14.5px;line-height:27px;color:var(--muted)}
.btn-solid{position:absolute;background:linear-gradient(#2a92de,var(--blue-dark));color:var(--white);font-family:"Montserrat",sans-serif;font-weight:500;text-align:center}
.about .btn-solid{left:543px;top:308px;width:138px;height:38px;line-height:38px;font-size:14px}

/* services */
.services{top:1042px;height:479px;background:radial-gradient(ellipse at 80% 70%,#3aa6ee,var(--blue) 55%,#0f74c6)}
.services::before{content:"";position:absolute;left:564px;top:0;border:36px solid transparent;border-top:30px solid var(--white);border-bottom:0}
.section-title{position:absolute;left:0;width:1200px;text-align:center;font-family:"Nunito Sans",sans-serif;font-weight:400;font-size:27px}
.services .section-title{top:44px;color:var(--white)}
.card{position:absolute;top:93px;width:302px;height:346px;background:var(--white)}
.card-photo{height:167px}
.card h3{margin-top:22px;text-align:center;font-family:"Nunito Sans",sans-serif;font-weight:400;font-size:19px;color:var(--blue-title)}
.card p{margin:12px auto 0;width:262px;height:45px;overflow:hidden;text-align:center;font-size:12.5px;line-height:15px;color:var(--muted)}
.card .link{display:block;margin:18px auto 0;width:110px;text-align:center;font-family:"Montserrat",sans-serif;font-size:14px;color:var(--blue-dark);padding-bottom:5px;border-bottom:2px solid #3aa0e6}

/* contact form */
.contact{top:1521px;height:444px}
.contact .section-title{top:50px;font-family:"Montserrat",sans-serif;font-weight:600;font-size:23px;color:var(--blue-title)}
.field{position:absolute;background:#f6f6f6;border:1px solid var(--line);font-size:14px;color:#777;padding:11px 15px}
.contact .btn-solid{left:512px;top:337px;width:169px;height:39px;line-height:39px;font-size:16px;font-weight:600}

/* it support */
.support{top:1965px;height:385px;background:var(--light-gray)}
.support-photo{position:absolute;left:587px;top:0;width:613px;height:385px;clip-path:polygon(0 0,100% 0,100% 100%,131px 100%);background:radial-gradient(circle at 45% 70%,#ffcf5a 0%,#e0832c 10%,#2d3d6a 35%,#0e1733 75%)}
.support h2{position:absolute;left:128px;top:72px;font-family:"Montserrat",sans-serif;font-weight:500;font-size:25px;color:#222}
.support p{position:absolute;left:129px;top:113px;width:462px;font-size:12.5px;line-height:22px;color:#666}
.tick{position:absolute;font-family:"Montserrat",sans-serif;font-size:11px;color:#444;white-space:nowrap}
.tick::before{content:"→";color:var(--blue);margin-right:5px}
.btn-outline{position:absolute;left:129px;top:295px;width:125px;height:32px;border:2px solid #555;font-family:"Montserrat",sans-serif;font-size:12px;line-height:28px;text-align:center;color:#333}

/* testimonials */
.testimonials{top:2350px;height:369px}
.testimonials .section-title{top:64px;color:var(--blue-title);font-size:25px;letter-spacing:1px}
.quote{position:absolute;left:300px;top:127px;width:600px;text-align:center;font-size:16px;line-height:33px;color:#8c8c8c}
.quote b{color:var(--blue);font-family:Georgia,serif;font-size:34px;line-height:0}
.author{position:absolute;top:247px;left:0;width:1200px;text-align:center;font-size:16px;color:#333}

/* footer */
footer{top:2719px;height:406px;background:linear-gradient(#c9c9c9,#9c9c9c);color:var(--white)}
.col{position:absolute;top:66px}
.col h4{font-family:"Montserrat",sans-serif;font-weight:400;font-size:18px;margin-bottom:8px;letter-spacing:.5px}
.col li{list-style:none;font-size:14px;line-height:27.5px}
.social{display:flex;gap:9px;margin-top:8px}
.social i{width:34px;height:34px;border-radius:50%;background:#b5b5b5;border:1px solid #d8d8d8}
.rule{position:absolute;left:133px;top:302px;width:934px;height:1px;background:#b3b3b3}
.copy{position:absolute;top:325px;width:1200px;text-align:center;font-size:11px;color:#ececec}
</style>
</head>
<body>

<section class="hero">
  <div class="hero-photo" role="img" aria-label="Hands touching a glowing blue tablet screen"></div>
  <div class="brand"><span class="brand-mark"></span><span class="brand-name">Kelvanbrook</span></div>
  <div class="menu-toggle"><span></span><span></span><span></span></div>
  <ul class="menu">
    <li>HOME</li><li>ABOUT US</li><li>SUPPORT</li><li class="has-sub">SERVICES</li><li>PROJECTS</li><li>CONTACT</li>
  </ul>
  <h1 class="hero-title">FLEXIBLE SOLUTIONS FOR YOUR<br>BUSINESS NEEDS</h1>
  <div class="btn-ghost">QUICK CONTACT</div>
  <div class="dots"><i></i><i></i><i></i><i></i></div>
</section>

<section class="about">
  <div class="about-art" role="img" aria-label="Silver and blue 3D cube with floating blocks"></div>
  <h2>About Kelvanbrook Development Group, Inc</h2>
  <p>Kelvanbrook is a technology solution provider based in Brennan Harbor, Oregon. Our goal is to make technology a non-issue for individuals and small to medium size businesses ranging from 5 to 150 Users. We have the experience, the tools, high-level technology solutions and training to power your business and your work force. We understand that all business's have one goal in common! A Return on Investment</p>
  <div class="btn-solid">READ MORE</div>
</section>

<section class="services">
  <h2 class="section-title">OUR SERVICES</h2>
  <article class="card" style="left:129px">
    <div class="card-photo" role="img" aria-label="Person holding a tablet with digital interface" style="background:linear-gradient(135deg,#1e5c99,#0d2d52)"></div>
    <h3>Managed IT Solutions</h3>
    <p>Our staff will design, service, administer and maintain your IT needs. We are well versed on all major operating system, and platforms.</p>
    <span class="link">LEARN MORE</span>
  </article>
  <article class="card" style="left:448px">
    <div class="card-photo" role="img" aria-label="Technician working in a server room" style="background:linear-gradient(135deg,#3a5f7a,#1a2e3c)"></div>
    <h3>Remote Diagnostic</h3>
    <p>Do you need a quick solution to a technical problem? With our live remote-assistance tool, a member of our support team can help.</p>
    <span class="link">LEARN MORE</span>
  </article>
  <article class="card" style="left:767px">
    <div class="card-photo" role="img" aria-label="Engineer with laptop beside server racks" style="background:linear-gradient(135deg,#c7ccd2,#7d8792)"></div>
    <h3>IT Infrastructure Design</h3>
    <p>Do you have more than one site? Do you need remote access? We can design and implement LANS/WANS and VPN's.</p>
    <span class="link">LEARN MORE</span>
  </article>
</section>

<section class="contact">
  <h2 class="section-title">QUICK CONTACT FORM</h2>
  <div class="field" style="left:202px;top:112px;width:392px;height:44px">First Name</div>
  <div class="field" style="left:604px;top:112px;width:394px;height:44px">Last Name</div>
  <div class="field" style="left:202px;top:164px;width:392px;height:44px">Email address</div>
  <div class="field" style="left:604px;top:164px;width:394px;height:44px">Phone</div>
  <div class="field" style="left:202px;top:221px;width:796px;height:91px">Message</div>
  <div class="btn-solid">SUBMIT</div>
</section>

<section class="support">
  <div class="support-photo" role="img" aria-label="Hand holding a glowing network of connected points"></div>
  <h2>IT SUPPORT SOLUTIONS</h2>
  <p>Mauris vel lacus vitae felis vestibulum volutpat Etiam est nunc venenatis in tristique eu imperdiet ac nisl Cum sociis natoque penatibus et magnis dis parturient montes nascetur ridiculus mus In iaculis facilisis massa</p>
  <span class="tick" style="left:125px;top:211px">NETWORK ADMINISTRATION</span>
  <span class="tick" style="left:327px;top:211px">NETWORK CABLING</span>
  <span class="tick" style="left:510px;top:211px">ANTIVIRUS SOLUTIONS</span>
  <span class="tick" style="left:125px;top:244px">DESKTOP SUPPORT</span>
  <span class="tick" style="left:327px;top:244px">WIRELESS NETWORKS</span>
  <span class="tick" style="left:510px;top:244px">NETWORK SECURITY</span>
  <div class="btn-outline">READ MORE</div>
</section>

<section class="testimonials">
  <h2 class="section-title">TESTIMONIALS</h2>
  <svg class="abs" style="left:155px;top:158px" width="26" height="60" viewBox="0 0 26 60"><polyline points="24,2 2,30 24,58" fill="none" stroke="#555" stroke-width="2"/></svg>
  <svg class="abs" style="left:1022px;top:158px" width="26" height="60" viewBox="0 0 26 60"><polyline points="2,2 24,30 2,58" fill="none" stroke="#555" stroke-width="2"/></svg>
  <p class="quote"><b>“</b> Morbi diam mauris viverra in gravida eu mattis in ante Morbi eget arcu Morbi porta libero id ullamcorper nonummy nibh ligula pulvinar metus eget consectetuer augue <b>”</b></p>
  <p class="author">-By Author Name</p>
</section>

<footer>
  <div class="col" style="left:150px"><h4>COMPANY</h4><ul><li>Home</li><li>About Us</li><li>Our Services</li><li>Why Us</li><li>Contact</li></ul></div>
  <div class="col" style="left:356px"><h4>RESOURCES</h4><ul><li>Support</li><li>Solutions</li><li>Clients</li><li>Testimonials</li></ul></div>
  <div class="col" style="left:560px"><h4>CONTACT INFO</h4><ul><li>412 Marlow Ridge Road Suite B20</li><li>Ashford Falls, PA 19380</li><li>(555) 318-4420</li><li>info@kelvanbrook.com</li></ul></div>
  <div class="col" style="left:846px"><h4>FOLLOW US</h4><div class="social"><i></i><i></i><i></i><i></i></div></div>
  <div class="rule"></div>
  <p class="copy">© 2017 Company Name &nbsp;All rights reserved &nbsp;Term of Use</p>
</footer>

</body>
</html>
```